Business Card Design Project

We are rebranding an existing automotive collision repair business. The business is called dent haven. I have attached logo but I'm not tied to that. I want to leave this wide open.

I want this card to say we are professional, competent, cutting edge. We are focused on customers and use a lot of the latest technology to make the customer experience different. We sign customers in on iPads. Paperwork I signed electronically and updates are sent via text, email, logging on a website or as they wish. I want this innovation and image to come through in our cards

Target Market(s)

60%. Women 40% men. Age 35-60

Industry/Entity Type

Automotive

Requirements
Must have
• The card must have name, title, phone,email, cell, web page

```html
<!DOCTYPE html>
<html lang="en">
<head>
<meta charset="utf-8">
<title>Dent Haven – Business Card</title>
<link rel="stylesheet" href="https://fonts.googleapis.com/css2?family=Open+Sans:wght@400;600;700;800&display=swap">
<style>
  :root {
    --bg: #3a3a3a;
    --green-dark: #1f7d2b;
    --green-mid: #4fa227;
    --green-light: #86c225;
    --green-pale: #c9e6a0;
    --ink: #111111;
    --ink-soft: #333333;
    --white: #ffffff;
    --card-w: 680px;
    --card-h: 388px;
    --radius: 26px;
  }
  * { box-sizing: border-box; margin: 0; padding: 0; }
  html, body {
    width: 1200px; height: 900px; overflow: hidden;
    background: var(--bg);
    font-family: "Open Sans", Arial, sans-serif;
  }
  .canvas { position: relative; width: 1200px; height: 900px; }
  .card {
    position: absolute;
    width: var(--card-w); height: var(--card-h);
    border-radius: var(--radius);
    overflow: hidden;
  }

  /* Back side */
  .card-back {
    left: 460px; top: 50px;
    background: linear-gradient(120deg, var(--green-dark) 0%, var(--green-mid) 45%, var(--green-light) 100%);
    color: var(--white);
  }
  .card-back .brand {
    position: absolute; left: 0; right: 0; top: 138px;
    text-align: center;
  }
  .brand-name {
    font-weight: 800; font-size: 46px; letter-spacing: -0.5px; line-height: 1;
  }
  .brand-tagline {
    margin-top: 8px;
    font-weight: 700; font-size: 11px; letter-spacing: 3px; text-transform: uppercase;
  }
  .card-back .brand-name, .card-back .brand-tagline { color: var(--white); }
  .card-back .site {
    position: absolute; left: 0; right: 0; bottom: 42px;
    text-align: center; font-size: 19px; letter-spacing: 0.5px;
  }

  /* Front side */
  .card-front { left: 60px; top: 462px; background: var(--white); }
  .front-wave { position: absolute; inset: 0; width: 100%; height: 100%; }
  .card-front .brand { position: absolute; left: 40px; top: 46px; }
  .card-front .brand-name { color: var(--green-mid); font-size: 38px; }
  .card-front .brand-tagline { color: var(--ink-soft); font-size: 9px; letter-spacing: 2.6px; margin-top: 6px; }

  .person { position: absolute; right: 44px; top: 96px; text-align: right; }
  .person-name { font-weight: 700; font-size: 25px; color: var(--ink); }
  .person-title { font-size: 16px; color: var(--ink-soft); margin-top: 2px; }

  .contact-list {
    position: absolute; left: 36px; top: 212px;
    list-style: none; color: var(--white); font-size: 15px; line-height: 24px;
  }
  .contact-list li { display: flex; align-items: center; gap: 10px; }
  .contact-list svg { width: 13px; height: 13px; fill: var(--white); flex: none; }

  .address {
    position: absolute; right: 40px; bottom: 30px;
    color: var(--white); font-size: 15px; line-height: 22px; text-align: right;
  }
</style>
</head>
<body>
<main class="canvas">

  <section class="card card-back" aria-label="Back of business card">
    <div class="brand">
      <div class="brand-name">Dent Haven</div>
      <div class="brand-tagline">Smart repairs, made simple</div>
    </div>
    <div class="site">www.denthaven.com</div>
  </section>

  <section class="card card-front" aria-label="Front of business card">
    <svg class="front-wave" viewBox="0 0 680 388" preserveAspectRatio="none" aria-hidden="true">
      <defs>
        <linearGradient id="frontGreen" x1="0" y1="0" x2="1" y2="0.4">
          <stop offset="0" stop-color="#1f7d2b"/>
          <stop offset="0.55" stop-color="#4fa227"/>
          <stop offset="1" stop-color="#86c225"/>
        </linearGradient>
      </defs>
      <path d="M0,150 C140,128 290,160 410,222 C520,278 600,296 680,300 L680,388 L0,388 Z" fill="url(#frontGreen)"/>
      <path d="M0,146 C140,124 290,156 410,218 C520,274 600,292 680,296" fill="none" stroke="#c9e6a0" stroke-width="4"/>
      <path d="M0,156 C140,134 290,166 410,228 C520,284 600,302 680,306" fill="none" stroke="#222222" stroke-width="2"/>
    </svg>

    <div class="brand">
      <div class="brand-name">Dent Haven</div>
      <div class="brand-tagline">Smart repairs, made simple</div>
    </div>

    <div class="person">
      <div class="person-name">Daniel Moore</div>
      <div class="person-title">Vice President</div>
    </div>

    <ul class="contact-list">
      <li><svg viewBox="0 0 16 16"><path d="M3 1l3 3-2 2c1 2 3 4 5 5l2-2 3 3-2 3C7 15 1 9 1 3z"/></svg>800-555-0142</li>
      <li><svg viewBox="0 0 16 16"><rect x="1" y="11" width="3" height="4"/><rect x="6" y="7" width="3" height="8"/><rect x="11" y="2" width="3" height="13"/></svg>800-555-0142</li>
      <li><svg viewBox="0 0 16 16"><path d="M1 3h14v10H1z M2 4l6 5 6-5" fill="none" stroke="#fff" stroke-width="1.5"/></svg>info@denthaven.com</li>
      <li><svg viewBox="0 0 16 16"><circle cx="8" cy="8" r="6.5" fill="none" stroke="#fff" stroke-width="1.5"/><path d="M1.5 8h13M8 1.5c-3 3.5-3 9.5 0 13M8 1.5c3 3.5 3 9.5 0 13" fill="none" stroke="#fff" stroke-width="1.2"/></svg>www.denthaven.com</li>
    </ul>

    <div class="address">
      4180 E. Harbor Lane. STE 210<br>
      PMB#300 Tempe, AZ 85281
    </div>
  </section>

</main>
</body>
</html>
```